Business card por a urban DJ, up scale audience target

Need a sober design, modern, conservative colors but i can consider some options, y play rnb, hip hop, EDM and top40.

Business card for contact and personal info, double sided, use logo attrached please; im 42 so i need a card acording to my age an target audience.

Target Market(s)

Adult people, up scale audience

Industry/Entity Type

Music Download

Contact Information for Business Card

Cel (318) 4207265518 www.lumadrift.com

Requirements
Must have
• open mind
Nice to have
• open mind
Should not have
• DJ

```html
<!DOCTYPE html>
<html lang="en">
<head>
<meta charset="utf-8">
<title>Luma business card</title>
<link href="https://fonts.googleapis.com/css2?family=Open+Sans:wght@400;600;700&display=swap" rel="stylesheet">
<style>
  :root {
    --page: #e9e7e3;
    --paper: #f4f4f4;
    --paper-shade: #dcdcdc;
    --ink: #3a3a3a;
    --ink-deep: #262626;
    --ink-soft: #555555;
    --light-text: #f2f2f2;
    --muted-text: #cfcfcf;
  }
  * { box-sizing: border-box; margin: 0; padding: 0; }
  html, body { width: 1200px; height: 902px; overflow: hidden; }
  body {
    background: var(--page);
    font-family: "Open Sans", Arial, sans-serif;
    position: relative;
  }
  .card {
    position: absolute;
    left: 280px;
    width: 640px;
    height: 366px;
    overflow: hidden;
    box-shadow: 0 6px 18px rgba(0,0,0,0.18);
  }
  /* front side */
  .card-front {
    top: 60px;
    background: linear-gradient(160deg, #ffffff 0%, var(--paper) 55%, var(--paper-shade) 100%);
  }
  .card-front .brand {
    position: absolute;
    left: 0; right: 0; top: 120px;
    display: flex; align-items: center; justify-content: center; gap: 18px;
  }
  .card-front .brand-square {
    width: 34px; height: 34px; background: var(--ink);
  }
  .card-front .brand-name {
    font-weight: 700; font-size: 78px; letter-spacing: 6px; color: var(--ink); line-height: 1;
  }
  .card-front .rule {
    position: absolute; left: 0; right: 0; top: 306px; height: 3px; background: var(--ink);
  }
  .card-front .band {
    position: absolute; left: 0; right: 0; top: 318px; bottom: 0;
    background: linear-gradient(90deg, var(--ink-soft), var(--ink-deep));
  }
  /* back side */
  .card-back {
    top: 476px;
    background: linear-gradient(160deg, #4a4a4a 0%, var(--ink) 45%, var(--ink-deep) 100%);
    color: var(--light-text);
  }
  .card-back .brand {
    position: absolute; left: 36px; top: 152px;
    display: flex; align-items: center; gap: 14px;
  }
  .card-back .brand-square { width: 26px; height: 26px; background: var(--light-text); }
  .card-back .brand-name {
    font-weight: 700; font-size: 58px; letter-spacing: 4px; color: var(--light-text); line-height: 1;
  }
  .card-back .divider {
    position: absolute; left: 300px; top: 40px; width: 1px; height: 224px; background: #8a8a8a;
  }
  .card-back .person { position: absolute; left: 326px; top: 44px; }
  .card-back .person-name { font-size: 25px; font-weight: 700; line-height: 1.15; }
  .card-back .person-role { font-size: 18px; font-weight: 400; color: var(--muted-text); }
  .card-back .contact-list {
    position: absolute; left: 326px; top: 146px; list-style: none;
  }
  .card-back .contact-list li {
    display: flex; align-items: center; gap: 10px;
    font-size: 15px; line-height: 26px; color: var(--light-text);
  }
  .card-back .contact-list svg { width: 14px; height: 14px; flex: none; }
  .card-back .rule {
    position: absolute; left: 0; right: 0; top: 292px; height: 3px; background: var(--paper);
  }
  .card-back .band {
    position: absolute; left: 0; right: 0; top: 306px; bottom: 0;
    background: linear-gradient(180deg, #ffffff, var(--paper-shade));
  }
  .card-back .band-line {
    position: absolute; left: 0; right: 0; top: 336px; height: 1px; background: #9a9a9a;
  }
</style>
</head>
<body>
  <section class="card card-front" aria-label="Card front">
    <div class="brand">
      <span class="brand-square"></span>
      <span class="brand-name">LUMA</span>
    </div>
    <div class="rule"></div>
    <div class="band"></div>
  </section>

  <section class="card card-back" aria-label="Card back">
    <div class="brand">
      <span class="brand-square"></span>
      <span class="brand-name">LUMA</span>
    </div>
    <div class="divider"></div>
    <div class="person">
      <p class="person-name">Theo Varga</p>
      <p class="person-role">Managing Director</p>
    </div>
    <ul class="contact-list">
      <li>
        <svg viewBox="0 0 14 14"><rect width="14" height="14" rx="2" fill="#f2f2f2"/><path d="M4 3.5h2l.7 2-1.2.8a5 5 0 0 0 2.2 2.2l.8-1.2 2 .7v2c0 .5-.5 1-1 1A7 7 0 0 1 3 4.5c0-.5.5-1 1-1z" fill="#333"/></svg>
        (318) 4207265518
      </li>
      <li>
        <svg viewBox="0 0 14 14"><rect width="14" height="14" rx="2" fill="#f2f2f2"/><rect x="3" y="4" width="8" height="6" fill="none" stroke="#333" stroke-width="1.2"/><path d="M3 4l4 3.2L11 4" fill="none" stroke="#333" stroke-width="1.2"/></svg>
        info@lumadrift.com
      </li>
      <li>
        <svg viewBox="0 0 14 14"><rect width="14" height="14" rx="2" fill="#f2f2f2"/><circle cx="7" cy="7" r="4" fill="none" stroke="#333" stroke-width="1.2"/><path d="M3 7h8M7 3c-2 2.5-2 5.5 0 8M7 3c2 2.5 2 5.5 0 8" fill="none" stroke="#333" stroke-width="1"/></svg>
        www.lumadrift.com
      </li>
      <li>
        <svg viewBox="0 0 14 14"><rect width="14" height="14" rx="2" fill="#f2f2f2"/><path d="M7 11.5S4 8.2 4 6a3 3 0 0 1 6 0c0 2.2-3 5.5-3 5.5z" fill="#333"/><circle cx="7" cy="6" r="1" fill="#f2f2f2"/></svg>
        118 Harbor Row St, Calder MD 214
      </li>
    </ul>
    <div class="rule"></div>
    <div class="band"></div>
    <div class="band-line"></div>
  </section>
</body>
</html>
```